University Student Business Card

Looking for a professional university student business card. Student is studying business with a focus on marketing. Some combination using a monogram and/or full name on the front with full name, university details and contact information on the back. Card should be modern design for a young professional. Prefer use of royal blue, black and white but am open to other uses of colour palette if it reinforces young/trendy style. Initials for a monogram are: KR. Full details will be provided in private consultation with designer(s).

Target Market(s)

Professional business people, marketers, advertisers, consultants

Industry/Entity Type

Business, marketing

Contact Information for Business Card

Monogram or personal logo, full name, university name, program of study, phone number, email address, pathfolio address

Other font styles liked:
• Open to suggestion to fulfill above requirements

Colors
0054AA
0677BA
7BADD7
CADEEF
E8F1F8

Requirements
Must have
• Monogram using letters K and R, and incorporate the business card details listed in the brief (specific details including personal contact info will be shared with successful designer to ensure privacy)
Nice to have
• Personal brand using monogram or personal logo (not a business logo)

```html
<!DOCTYPE html>
<html lang="en">
<head>
<meta charset="utf-8">
<title>Kieran Rowe – Business Card</title>
<link href="https://fonts.googleapis.com/css2?family=Montserrat:wght@600&family=Arimo:wght@400&display=swap" rel="stylesheet">
<style>
  :root {
    --royal: #0054AA;
    --link-blue: #0677BA;
    --ink: #3a3a3a;
    --rule: #d4d4d4;
    --card: #f7f7f7;
    --backdrop: #2a2a2a;
  }
  * { margin: 0; padding: 0; box-sizing: border-box; }
  html, body {
    width: 1200px; height: 900px; overflow: hidden;
    background: var(--backdrop);
  }
  .stage {
    position: relative; width: 1200px; height: 900px;
    display: flex; align-items: center; justify-content: center; gap: 50px;
  }
  .card {
    width: 525px; height: 300px;
    background: var(--card);
    display: flex; flex-direction: column; align-items: center; justify-content: center;
    text-align: center;
    box-shadow: 0 10px 30px rgba(0,0,0,.45);
  }
  .heading {
    font-family: "Montserrat", sans-serif; font-weight: 600;
    color: var(--royal); letter-spacing: .5px;
  }
  .detail {
    font-family: "Arimo", sans-serif; font-weight: 400;
    color: var(--ink); font-size: 15px; line-height: 1.3;
  }
  .divider {
    width: 70px; height: 1px; background: var(--rule); margin: 11px 0;
  }

  /* back */
  .card-back .heading { font-size: 24px; }

  /* front */
  .monogram {
    font-family: "Montserrat", sans-serif; font-weight: 600;
    color: var(--royal); font-size: 96px; line-height: 1; letter-spacing: 2px;
    margin-bottom: 18px;
  }
  .card-front .heading { font-size: 19px; }
  .card-front .role { font-size: 13px; }
  .profile { display: flex; align-items: center; gap: 8px; }
  .profile-dot {
    width: 18px; height: 18px; border-radius: 50%; background: var(--link-blue);
  }
</style>
</head>
<body>
  <main class="stage">
    <section class="card card-back">
      <h2 class="heading">UNIVERSITY NAME</h2>
      <div class="divider"></div>
      <p class="detail">218, Elmfield Avenue East<br>30817,Northland</p>
      <div class="divider"></div>
      <p class="detail">055-210 384 617<br>info@rowemail.com<br>www.kieranrowe.net</p>
    </section>

    <section class="card card-front">
      <div class="monogram">KR</div>
      <h1 class="heading">KIERAN ROWE</h1>
      <p class="detail role">Business Marketing</p>
      <div class="divider"></div>
      <p class="detail profile"><span class="profile-dot"></span>pathfolio.com/name</p>
    </section>
  </main>
</body>
</html>
```